Beautify our counselling web application

I have a web application in development and at the moment it is very plain.
It has being developed with laravel and vue. I need a simple design for the user interface to make it look more sleek and professional. I will need someone who is able to code the design as part of the service. The app is very low-cost for voluntary and social enterprise services and we don't have a lot of money so I need someone who is just starting out or someone with a big heart.
I have uploaded current pages to show the contents.
I will tip for good work.

Target Market(s)

Counsellors and psychotherapists

Industry/Entity Type

SaaS

Font styles to use
Serif
Sans Serif

Colors
0054AA
0677BA
7BADD7
CADEEF
E8F1F8

Requirements
Must have
• Ability to code the design into the current site
Nice to have
• elegant, modern. cool, profession. nice examples include merovaultix.com quillbanter.com fenrodu.com
Should not have
• corny literal 90s icons, icons with more than one colour using primary colours

```html
<!DOCTYPE html>
<html lang="en">
<head>
<meta charset="utf-8">
<title>Counselling App – Interface Screens</title>
<link rel="stylesheet" href="https://fonts.googleapis.com/css2?family=Figtree:wght@400;500;600;700;800&display=swap">
<style>
:root{
  --navy:#0d3168;
  --title:#134f8f;
  --primary:#0054AA;
  --mid:#0677BA;
  --cyan:#00a8d0;
  --light:#CADEEF;
  --pale:#E8F1F8;
  --panel-bg:#eef5fb;
  --ink:#14233a;
  --link:#0e5ba8;
  --white:#ffffff;
}
*{box-sizing:border-box;margin:0;padding:0}
html,body{width:746px;height:1200px;overflow:hidden;background:#fff;font-family:"Figtree",sans-serif;color:var(--ink)}
.screen{position:absolute;left:24px;width:698px;height:356px;border:7px solid var(--navy);border-radius:30px;background:var(--panel-bg);overflow:hidden}
.screen--dashboard{top:28px}
.screen--caseload{top:407px}
.screen--client{top:785px}
.app-header{position:absolute;left:0;top:0;width:100%;height:43px;background:var(--white)}
.app-title{position:absolute;left:14px;top:12px;font-size:15.5px;font-weight:700;color:var(--title);letter-spacing:.1px}
.header-btn{position:absolute;top:14px;width:22px;height:22px;border-radius:50%;background:var(--mid);display:flex;align-items:center;justify-content:center}
.header-btn--help{left:571px}
.header-btn--avatar{left:608px;background:linear-gradient(135deg,#7a6a5e,#3e3430)}
.header-btn--logout{left:640px}
.sidebar{position:absolute;left:0;top:43px;width:134px;height:306px;background:linear-gradient(170deg,#0d4f9c 0%,#0677BA 45%,#04aad6 100%)}
.nav-item{position:absolute;left:23px;font-size:10.5px;color:var(--white);font-weight:500}
.nav-item--active{font-weight:800}
.collapse-tab{position:absolute;left:119px;width:18px;height:14px;border-radius:7px 0 0 7px;background:var(--white);color:var(--title);font-size:9px;line-height:13px;text-align:center}
.content{position:absolute;left:142px;top:55px;width:531px;height:276px;background:var(--white);border-radius:14px}
.page-title{position:absolute;left:13px;top:15px;font-size:15px;font-weight:600;color:var(--title)}
.welcome{position:absolute;left:7px;top:41px;width:518px;height:38px;background:var(--cyan);color:var(--white);font-size:8.5px;font-weight:700;display:flex;align-items:center;justify-content:center;box-shadow:0 2px 4px rgba(0,0,0,.15)}
.info-card{position:absolute;top:96px;width:159px;height:116px;border-radius:7px;background:#f0f9fd}
.info-card--raised{background:var(--white);box-shadow:0 1px 5px rgba(0,0,0,.15)}
.card-icon{position:absolute;left:11px;top:14px;width:21px;height:21px;border-radius:50%;background:#d3eef8;display:flex;align-items:center;justify-content:center}
.card-title{position:absolute;left:40px;top:20px;font-size:9px;font-weight:600;color:var(--title)}
.card-btn{position:absolute;left:17px;top:47px;padding:4px 7px;border-radius:8px;background:var(--mid);color:var(--white);font-size:5.5px;font-weight:600}
.card-empty{position:absolute;left:20px;top:72px;font-size:8px;font-weight:600;color:var(--title)}
.search-bar{position:absolute;left:97px;top:14px;width:158px;height:21px;border:1px solid #b9c3cf;display:flex;font-size:8px;color:#7e8a99}
.search-filter{width:50px;border-right:1px solid #b9c3cf;display:flex;align-items:center;padding-left:8px}
.search-input{display:flex;align-items:center;padding-left:9px}
.table-area{position:absolute;left:7px;top:46px;width:518px;height:222px;background:var(--panel-bg);border-radius:12px;overflow:hidden}
.table-row{position:absolute;left:0;width:518px;display:grid;grid-template-columns:10px 27px 36px 70px 39px 55px 49px 65px 54px 68px 45px;align-items:center;font-size:6px;color:var(--link);white-space:nowrap}
.table-row--head{top:15px;height:12px;font-size:7px;font-weight:700;color:var(--ink)}
.table-row--selected{background:var(--cyan);color:var(--white);box-shadow:0 1px 4px rgba(0,0,0,.2)}
.risk-box{width:8px;height:8px;border-radius:1px;background:#0b9ed0}
.client-cell{display:flex;align-items:center;gap:4px}
.client-avatar{width:9px;height:9px;border-radius:50%;background:linear-gradient(#c9a98e,#3b5a82);flex:none}
.contacts-pill{display:inline-block;width:35px;height:13px;border-radius:7px;background:var(--navy);color:var(--white);font-size:4.8px;font-weight:700;line-height:13px;text-align:center}
.breadcrumb{position:absolute;left:13px;top:15px;font-size:15px;font-weight:600;color:var(--title)}
.breadcrumb small{font-size:11px;font-weight:500}
.tab{position:absolute;top:40px;height:15px;border-radius:8px;font-size:5.5px;font-weight:600;display:flex;align-items:center;justify-content:center;border:1px solid var(--mid);color:var(--link)}
.tab--solid{background:var(--mid);color:var(--white)}
.tab--dark{background:var(--primary);border-color:var(--primary);color:var(--white)}
.tab--muted{background:var(--pale);border-color:var(--pale)}
.episode-box{position:absolute;left:7px;top:63px;width:518px;height:204px;background:var(--panel-bg);border-radius:12px}
.episode-label{position:absolute;left:10px;top:19px;font-size:7px;font-weight:600}
.episode-start{position:absolute;left:349px;top:21px;font-size:7px}
.episode-start b{font-weight:700}
.end-btn{position:absolute;left:450px;top:16px;width:49px;height:15px;border-radius:8px;background:#d0121b;color:var(--white);font-size:5.5px;font-weight:700;display:flex;align-items:center;justify-content:center}
.record-pill{position:absolute;width:60px;height:15px;border-radius:8px;color:var(--white);font-size:5.3px;font-weight:700;display:flex;align-items:center;justify-content:center}
.row-a{top:62px}.row-b{top:95px}
</style>
</head>
<body>

<section class="screen screen--dashboard">
  <header class="app-header">
    <div class="app-title">Counselling App</div>
    <div class="header-btn header-btn--help"><svg width="12" height="12" viewBox="0 0 12 12"><circle cx="6" cy="6" r="5.5" fill="#fff"/><text x="6" y="9" font-size="8" font-weight="800" text-anchor="middle" fill="#0677BA" font-family="Figtree,sans-serif">?</text></svg></div>
    <div class="header-btn header-btn--avatar" role="img" aria-label="User profile photo"></div>
    <div class="header-btn header-btn--logout"><svg width="11" height="11" viewBox="0 0 11 11"><rect x="1.5" y="1" width="5" height="9" fill="#fff"/><path d="M6 5.5h4M8.5 4l1.5 1.5L8.5 7" stroke="#fff" stroke-width="1.2" fill="none"/></svg></div>
  </header>
  <nav class="sidebar">
    <div class="nav-item nav-item--active" style="top:23px">Dashboard</div>
    <div class="collapse-tab" style="top:23px">«</div>
    <div class="nav-item" style="top:49px">Caseload</div>
    <div class="nav-item" style="top:75px">Calendar</div>
    <div class="nav-item" style="top:101px">Address Book</div>
    <div class="nav-item" style="top:127px">Users</div>
    <div class="nav-item" style="top:153px">Services</div>
    <div class="nav-item" style="top:179px">Clients</div>
    <div class="nav-item" style="top:205px">Audit</div>
    <div class="nav-item" style="top:231px">Monitoring</div>
  </nav>
  <main class="content">
    <h1 class="page-title">Dashboard</h1>
    <div class="welcome">Welcome To Demo</div>
    <div class="info-card info-card--raised" style="left:8px">
      <div class="card-icon"><svg width="11" height="11" viewBox="0 0 11 11"><path d="M3 8V5a2.5 2.5 0 0 1 5 0v3l1 1H2z M4.5 9.5h2" stroke="#0a9bd0" stroke-width=".9" fill="none"/></svg></div>
      <div class="card-title">Notifications</div>
      <div class="card-btn">Create notification</div>
      <div class="card-empty">No notifications</div>
    </div>
    <div class="info-card" style="left:185px">
      <div class="card-icon"><svg width="11" height="11" viewBox="0 0 11 11"><rect x="1.5" y="2.5" width="8" height="7" fill="none" stroke="#0d3168" stroke-width=".9"/><path d="M1.5 4.5h8M3.5 1.5v2M7.5 1.5v2" stroke="#0d3168" stroke-width=".9"/></svg></div>
      <div class="card-title">Today</div>
      <div class="card-empty">No appointmentst</div>
    </div>
    <div class="info-card" style="left:364px">
      <div class="card-icon"><svg width="11" height="11" viewBox="0 0 11 11"><path d="M2 5h2v5H2zM4 5l2-3.5c1 0 1 1 .8 2H9.5v1.5L8.5 10H4" stroke="#0d3168" stroke-width=".9" fill="none"/></svg></div>
      <div class="card-title">Reviews</div>
      <div class="card-empty">No reviews!</div>
    </div>
  </main>
</section>

<section class="screen screen--caseload">
  <header class="app-header">
    <div class="app-title">Counselling App</div>
    <div class="header-btn header-btn--help"><svg width="12" height="12" viewBox="0 0 12 12"><circle cx="6" cy="6" r="5.5" fill="#fff"/><text x="6" y="9" font-size="8" font-weight="800" text-anchor="middle" fill="#0677BA" font-family="Figtree,sans-serif">?</text></svg></div>
    <div class="header-btn header-btn--avatar" role="img" aria-label="User profile photo"></div>
    <div class="header-btn header-btn--logout"><svg width="11" height="11" viewBox="0 0 11 11"><rect x="1.5" y="1" width="5" height="9" fill="#fff"/><path d="M6 5.5h4M8.5 4l1.5 1.5L8.5 7" stroke="#fff" stroke-width="1.2" fill="none"/></svg></div>
  </header>
  <nav class="sidebar">
    <div class="nav-item" style="top:23px">Dashboard</div>
    <div class="nav-item nav-item--active" style="top:49px">Caseload</div>
    <div class="collapse-tab" style="top:49px">«</div>
    <div class="nav-item" style="top:75px">Calendar</div>
    <div class="nav-item" style="top:101px">Address Book</div>
    <div class="nav-item" style="top:127px">Users</div>
    <div class="nav-item" style="top:153px">Services</div>
    <div class="nav-item" style="top:179px">Clients</div>
    <div class="nav-item" style="top:205px">Audit</div>
    <div class="nav-item" style="top:231px">Monitoring</div>
  </nav>
  <main class="content">
    <h1 class="page-title">Caseload</h1>
    <div class="search-bar"><div class="search-filter">Filter ⌄</div><div class="search-input">Search ....</div></div>
    <div class="table-area">
      <div class="table-row table-row--head"><span></span><span>Risk</span><span>Alerts</span><span>Clients</span><span>Id</span><span>Service</span><span>Therapist</span><span>Date Of Referral</span><span>First Contact</span><span>Previous Episode</span><span>Contacts</span></div>
      <div class="table-row" style="top:38px;height:14px"><span></span><span class="risk-box"></span><span></span><span class="client-cell"><i class="client-avatar" role="img" aria-label="Client avatar"></i>Colin Marsh</span><span>002</span><span>Demo Services 1</span><span>Owen</span><span>05/07/2022</span><span>20/09/2022</span><span></span><span><b class="contacts-pill">▶ Total: 3</b></span></div>
      <div class="table-row" style="top:65px;height:14px"><span></span><span class="risk-box"></span><span></span><span class="client-cell"><i class="client-avatar" role="img" aria-label="Client avatar"></i>Dennis Pryor</span><span>003</span><span>Demo Services 1</span><span>Owen</span><span>13/07/2022</span><span>20/09/2022</span><span></span><span><b class="contacts-pill">▶ Total: 2</b></span></div>
      <div class="table-row" style="top:92px;height:14px"><span></span><span class="risk-box"></span><span></span><span class="client-cell"><i class="client-avatar" role="img" aria-label="Client avatar"></i>Harriet Vale</span><span>004</span><span>Demo Services 1</span><span>Owen</span><span>19/07/2022</span><span>20/09/2022</span><span></span><span><b class="contacts-pill">▶ Total: 3</b></span></div>
      <div class="table-row" style="top:118px;height:14px"><span></span><span class="risk-box"></span><span></span><span class="client-cell"><i class="client-avatar" role="img" aria-label="Client avatar"></i>Tessa Quill</span><span>005</span><span>Demo Services 2</span><span>Ravi</span><span>17/07/2022</span><span>20/09/2022</span><span></span><span><b class="contacts-pill">▶ Total: 3</b></span></div>
      <div class="table-row table-row--selected" style="top:140px;height:24px"><span></span><span></span><span></span><span class="client-cell"><i class="client-avatar" role="img" aria-label="Client avatar"></i>Juno</span><span>006</span><span>Demo Services 2</span><span>Ravi</span><span>23/07/2022</span><span>20/09/2022</span><span>29/11/2022</span><span><b class="contacts-pill">▶ Total: 0</b></span></div>
      <div class="table-row" style="top:172px;height:14px"><span></span><span class="risk-box"></span><span></span><span class="client-cell"><i class="client-avatar" role="img" aria-label="Client avatar"></i>Marion Holloway</span><span>007</span><span>Demo Services 2</span><span>Ravi</span><span>06/07/2022</span><span>20/09/2022</span><span></span><span><b class="contacts-pill">▶ Total: 2</b></span></div>
    </div>
  </main>
</section>

<section class="screen screen--client">
  <header class="app-header">
    <div class="app-title">Counselling App</div>
    <div class="header-btn header-btn--help"><svg width="12" height="12" viewBox="0 0 12 12"><circle cx="6" cy="6" r="5.5" fill="#fff"/><text x="6" y="9" font-size="8" font-weight="800" text-anchor="middle" fill="#0677BA" font-family="Figtree,sans-serif">?</text></svg></div>
    <div class="header-btn header-btn--avatar" role="img" aria-label="User profile photo"></div>
    <div class="header-btn header-btn--logout"><svg width="11" height="11" viewBox="0 0 11 11"><rect x="1.5" y="1" width="5" height="9" fill="#fff"/><path d="M6 5.5h4M8.5 4l1.5 1.5L8.5 7" stroke="#fff" stroke-width="1.2" fill="none"/></svg></div>
  </header>
  <nav class="sidebar">
    <div class="nav-item" style="top:23px">Dashboard</div>
    <div class="nav-item nav-item--active" style="top:49px">Caseload</div>
    <div class="collapse-tab" style="top:49px">«</div>
    <div class="nav-item" style="top:75px">Calendar</div>
    <div class="nav-item" style="top:101px">Address Book</div>
    <div class="nav-item" style="top:127px">Users</div>
    <div class="nav-item" style="top:153px">Services</div>
    <div class="nav-item" style="top:179px">Clients</div>
    <div class="nav-item" style="top:205px">Audit</div>
    <div class="nav-item" style="top:231px">Monitoring</div>
  </nav>
  <main class="content">
    <h1 class="breadcrumb">Caseload <small>» Colin Marsh</small></h1>
    <div class="tab tab--dark" style="left:27px;width:49px">Work Space ˄</div>
    <div class="tab tab--solid" style="left:80px;width:60px">Client Information</div>
    <div class="tab" style="left:144px;width:48px">Client Record</div>
    <div class="tab" style="left:197px;width:60px">Client Progres</div>
    <div class="tab tab--muted" style="left:261px;width:60px">Payments</div>
    <div class="episode-box">
      <div class="episode-label">Episode</div>
      <div class="episode-start"><b>Started</b> : Wed Sep 14 2022</div>
      <div class="end-btn">End Episode</div>
      <div class="record-pill row-a" style="left:51px;background:#d45f7d">Session Record</div>
      <div class="record-pill row-a" style="left:122px;background:#b8703b">Assessment</div>
      <div class="record-pill row-a" style="left:193px;background:#b3a12b">Risk mangement</div>
      <div class="record-pill row-a" style="left:264px;background:#9c80a8">Summary</div>
      <div class="record-pill row-a" style="left:335px;background:#4a9a3a">Treatment Plan</div>
      <div class="record-pill row-a" style="left:406px;background:#4a9a9a">Consent</div>
      <div class="record-pill row-b" style="left:87px;background:#4f6bb0">Questionnaire</div>
      <div class="record-pill row-b" style="left:158px;background:#5a2fc0">Document</div>
      <div class="record-pill row-b" style="left:229px;background:#6b2d5a">Non-clinical note</div>
      <div class="record-pill row-b" style="left:300px;background:#2f6a4a">Safeguarding</div>
      <div class="record-pill row-b" style="left:371px;background:#9b3a96">Timeline</div>
    </div>
  </main>
</section>

</body>
</html>
```